PitchTally Webpages and Logo

See attached brief. Take the existing website www.pitchtally.co.uk and logo and transform these assets to:

Give people who arrive on the site for first time the confidence to sign-up easily and quickly
Allow regular returning users quick and easy placing of predictions and encourage them to share the PitchTally prediction on social networks and with their contacts
Convey the essence of a community working together to enjoyably come-up with smart predictions on sporting events
Work seamlessly and well across smartphones, tablets and desktop i.e. Should be Responsive Web Design
Updates

Target Market(s)

Users are sports fans with opinions
Primarily male and early twenties to mid-thirties
They are competitive - they want to beat their peers
Many are from outside the UK

Industry/Entity Type

Events

Logo Text

PitchTally

Coding

Coded - Design and coding required

Number of Pages Required

4 page

Font styles to use
Sans Serif

Requirements
Must have
• Responsive Web Design
• Mobile First
• HTML must work with dedicated bespoke application developed in ASP.NET using MS SQL underneath
• See Brief
Nice to have
• See brief
Should not have
• See brief

```html
<!DOCTYPE html>
<html lang="en">
<head>
<meta charset="utf-8">
<title>PitchTally</title>
<link href="https://fonts.googleapis.com/css2?family=Arimo:wght@400;700&family=Montserrat:wght@700;800&display=swap" rel="stylesheet">
<style>
:root{
  --ink:#000;
  --navy:#021a44;
  --blue:#0a5fd0;
  --blue-bright:#1e8cf0;
  --blue-dark:#073f9a;
  --btn:#0b3e8a;
  --teal:#1aa0d8;
  --white:#fff;
  --panel:#e4e4e4;
  --text-blue:#0b3f8c;
  --grass:#7cc22a;
}
*{box-sizing:border-box;margin:0;padding:0}
html,body{width:918px;height:1200px;overflow:hidden}
body{
  font-family:"Arimo",Arial,sans-serif;color:var(--white);position:relative;
  background:
    radial-gradient(ellipse 420px 260px at 459px 700px,rgba(30,120,255,.75),transparent 70%),
    radial-gradient(ellipse 700px 500px at 459px 760px,rgba(10,70,200,.55),transparent 75%),
    linear-gradient(180deg,#031b4a 0%,#02163d 40%,#041f58 70%,#021233 100%);
}
.topbar{position:absolute;left:0;top:0;width:918px;height:36px;background:var(--ink)}
.social{position:absolute;left:76px;top:11px;display:flex;gap:4px;font-size:8px;font-weight:700}
.social span{background:#eee;color:#222;border-radius:2px;padding:2px 4px;border:1px solid #bbb}
.social .fb{background:#4267b2;color:#fff;border-color:#4267b2}
.social .gap{margin-left:14px}
.clock{position:absolute;left:577px;top:12px;font-size:9px}
.clock b{font-family:"Montserrat",sans-serif;font-size:13px;margin-left:2px}
.tz{position:absolute;left:716px;top:4px;width:127px;height:28px;background:var(--teal);font-size:8px;line-height:28px;padding-left:13px}
.tz svg{position:absolute;right:8px;top:7px}
.brand{position:absolute;left:88px;top:58px;text-align:center;width:134px}
.brand .mark{display:block;width:30px;height:30px;border-radius:50%;background:var(--teal);margin:0 auto 24px}
.brand .name{font-family:"Montserrat",sans-serif;font-weight:800;font-size:17px;letter-spacing:.5px}
.banner{position:absolute;left:283px;top:70px;width:393px;height:85px;
  background:linear-gradient(100deg,#9ed63a,#5aa818 60%,#3f8a12);text-align:right;padding:8px 10px 0 0;
  font-family:"Montserrat",sans-serif;font-weight:800;color:#fff8c8}
.banner .l1{font-size:21px;line-height:26px}
.banner .l2{font-size:10px;margin-top:4px;background:#3c6b10;display:inline-block;padding:2px 6px}
.auth{position:absolute;left:729px;top:145px;font-size:9px;word-spacing:6px}
.nav{position:absolute;left:75px;top:176px;width:767px;height:39px;
  background:linear-gradient(180deg,#0a4db4,#0b6be0);display:flex;align-items:center;font-size:8px}
.nav a{color:#fff;text-decoration:none;margin-left:10px;margin-right:29px}
.kitty{position:absolute;right:28px;top:15px;display:flex;gap:6px;align-items:center}
.hero{position:absolute;left:75px;top:224px;width:767px;height:348px;
  background:radial-gradient(ellipse at 70% 40%,#3a3f48,#15171c 70%),#111;overflow:hidden}
.hero .photo{position:absolute;inset:0;
  background:linear-gradient(180deg,transparent 70%,#2d6a1a 88%,#3f8e20),
  radial-gradient(ellipse 220px 200px at 560px 180px,rgba(20,70,200,.65),transparent 70%)}
.hero h1{position:absolute;left:51px;top:162px;font-family:"Montserrat",sans-serif;font-weight:800;font-size:16px;letter-spacing:.3px}
.hero p{position:absolute;left:53px;top:190px;width:300px;font-size:10px;line-height:19px}
.play{position:absolute;left:47px;top:234px;width:97px;height:37px;background:linear-gradient(180deg,#0f5cc6,#0a3f94);font-size:10px;text-align:center;line-height:37px}
.deadline{position:absolute;left:49px;top:281px;font-size:10px}
.arrow{position:absolute;top:166px;width:20px;height:20px;border-radius:50%;background:#fff}
.dots{position:absolute;left:365px;top:305px;display:flex;gap:5px}
.dots i{width:8px;height:8px;border-radius:50%;border:1px solid #fff;background:#333}
.dots i:first-child{background:#b00}
.join{position:absolute;left:325px;top:600px;width:267px;height:48px;background:var(--white);
  color:var(--text-blue);font-family:"Montserrat",sans-serif;font-weight:800;font-size:17px;text-align:center;line-height:48px;letter-spacing:.5px}
.intro{position:absolute;left:200px;top:667px;width:518px;text-align:center;font-size:10px;line-height:19px}
.stat{position:absolute;top:728px;width:235px;height:146px;background:var(--white)}
.stat .head{height:44px;background:linear-gradient(180deg,#0b55c8,#0a47ad);font-size:10px;text-align:center;line-height:44px}
.stat .body{color:var(--text-blue);font-size:16px;text-align:center;line-height:27px;padding-top:26px}
.tips{position:absolute;left:75px;top:899px;width:767px;height:204px;background:var(--white)}
.tips h2{position:absolute;left:226px;top:18px;font-weight:400;font-size:17px;color:var(--text-blue)}
.tips .shares{position:absolute;left:453px;top:20px;display:flex;gap:8px;font-size:10px;color:#3b5a9a;align-items:center}
.tips .shares .tw{border:1px solid #aaa;border-radius:3px;padding:2px 5px;color:#222;font-weight:700}
.match{position:absolute;top:50px;width:173px;height:144px;background:var(--panel);color:var(--text-blue);text-align:center}
.match .crests{display:flex;justify-content:center;align-items:center;gap:18px;margin-top:13px;font-size:10px}
.match .crests i{width:42px;height:46px;border-radius:6px;display:block}
.match .when{margin-top:27px;font-size:10px}
.match .cta{margin:12px auto 0;width:131px;height:24px;background:var(--btn);color:#fff;font-size:10px;line-height:24px}
.foot{position:absolute;left:0;width:918px;text-align:center;font-size:10px}
.foot.links span{margin:0 6px}
.code{position:absolute;left:876px;top:1154px;font-size:10px}
</style>
</head>
<body>
<div class="topbar">
  <div class="social">
    <span>Follow @ScoreWatch</span><span>451K followers</span>
    <span class="fb gap">Like</span><span class="fb">Share</span><span>65k</span>
  </div>
  <div class="clock">THU DEC 18 2014 <b>05:13</b></div>
  <div class="tz">CHANGE TIME ZONE
    <svg width="14" height="14" viewBox="0 0 14 14"><circle cx="7" cy="7" r="6" fill="none" stroke="#fff" stroke-width="1.5"/><path d="M4 7h6M7.5 4.5 10 7l-2.5 2.5" fill="none" stroke="#fff" stroke-width="1.5"/></svg>
  </div>
</div>

<div class="brand"><span class="mark"></span><span class="name">PITCHTALLY</span></div>
<div class="banner" role="img" aria-label="Grass pitch banner with club name placeholder">
  <div class="l1">Your Team Name<br>Football Team</div>
  <div class="l2">MEMBERS OF ??? LEAGUE</div>
</div>
<div class="auth">LOGIN | REGISTER</div>

<nav class="nav">
  <a>HOME</a><a>ABOUT US</a><a>FIXUTERS</a><a>MINI LIGA</a><a>TABLES</a><a>KITTY</a><a>FAQ</a>
  <div class="kitty">KITTY: £1289
    <svg width="14" height="14" viewBox="0 0 14 14"><path d="M7 1 13 7H9v6H5V7H1z" fill="#fff"/></svg> 3%</div>
</nav>

<section class="hero">
  <div class="photo" role="img" aria-label="Footballer in blue kit volleying a ball on a floodlit pitch"></div>
  <h1>PREDICT 6 SCORESTO WIN £250,000</h1>
  <p>If the jackpot isn't won then we'll give the highest scoring player £5,000</p>
  <div class="play">PLAY NOW</div>
  <div class="deadline">Entries by 3:00pm, Saturday 20th December 2014.</div>
  <svg class="arrow" style="left:9px" viewBox="0 0 20 20"><path d="M12 5 7 10l5 5" fill="none" stroke="#333" stroke-width="2.5"/></svg>
  <svg class="arrow" style="left:738px" viewBox="0 0 20 20"><path d="M8 5l5 5-5 5" fill="none" stroke="#333" stroke-width="2.5"/></svg>
  <div class="dots"><i></i><i></i><i></i></div>
</section>

<div class="join">JOIN NOW</div>
<p class="intro">Predict results, scores and scorers for your free chance to win a £20 ShopSphere voucher every week. Overall season winner gets up to £1000 in ShopSphere vouchers! No entry fee and no catches.</p>

<div class="stat" style="left:75px"><div class="head">RESULT &nbsp; 100%</div><div class="body">REDBRIDGE UNITED<br>WIN</div></div>
<div class="stat" style="left:342px"><div class="head">SCORE &nbsp;&nbsp; 50%</div><div class="body">CLARET VILLA - 0<br>REDBRIDGE UNITED - 2</div></div>
<div class="stat" style="left:607px"><div class="head">1st GOAL &nbsp;80%</div><div class="body">Marlow C</div></div>

<section class="tips">
  <h2>PITCHTALLY HOT TIPS!</h2>
  <div class="shares"><span>Share</span><span class="tw">Tweet</span><span class="tw">1</span></div>
  <div class="match" style="left:6px"><div class="crests"><i style="background:#c8202a"></i>VS<i style="background:#8fb3de"></i></div><div class="when">Sat 20 Dec 2014 12:45 PM</div><div class="cta">Predict Score Now!</div></div>
  <div class="match" style="left:196px"><div class="crests"><i style="background:#222;border-radius:50%"></i>VS<i style="background:#f0a020"></i></div><div class="when">Sat 20 Dec 2014 12:45 PM</div><div class="cta">Predict Score Now!</div></div>
  <div class="match" style="left:390px"><div class="crests"><i style="background:#1a3a7a"></i>VS<i style="background:#d0202a"></i></div><div class="when">Sat 20 Dec 2014 12:45 PM</div><div class="cta">Predict Score Now!</div></div>
  <div class="match" style="left:582px"><div class="crests"><i style="background:#1a4aa0;border-radius:50%"></i>VS<i style="background:#1a3fa0"></i></div><div class="when">Sat 20 Dec 2014 12:45 PM</div><div class="cta">Predict Score Now!</div></div>
</section>

<p class="foot" style="top:1120px">Find us on SocialHub</p>
<p class="foot links" style="top:1142px"><span>About</span><span>Terms</span><span>Site Map</span><span>Privacy</span><span>Contact Us</span></p>
<p class="foot" style="top:1164px">Match fixtures reproduced under licence from League Fixtures Data Ltd. All rights reserved</p>
<div class="code">D4</div>
</body>
</html>
```